Ad for Cyber Security Company- Print Ad

We are looking for an awesome designer to create a one page advertisement for the Kelvora Security data analytics platform that will be featured in an upcoming security magazine. This is also going to be featured in an upcoming trade show. Kelvora Security produced the KELVORA platform to help companies unify their security environment and help them address Insider Threat, Fraud and Anomaly ID and resolution. KELVORA uses an an advanced ingestion engine, machine learning, and workflow automation to ensure the right people are getting the right info at the right time. We serve enterprise level customers, augmenting and enhancing, not replacing their existing security stack. We would like few or single image, clean, and open ad built around the tagline 'Make Security a Team Sport.' We would like the logo to be featured, and include our website address on the page (www.kelvorasecurity.net). See below for style guide.

Target Market(s)

Industry insiders, Chief Information Security Officers (CISO) and Technical directors.

Other font styles liked:
• See style guide, but we are open to suggestion.

Requirements
Must have
• A single image (minimum), Feature the provided logo, Include the tagline 'Make Security a Team Sport' and have the website somewhere on the ad. The image should focus on the conveying the message of "Make Security a Team Sport" and not be a generic security (padlock, network, etc.) image.
• See included style guide.

```html
<!DOCTYPE html>
<html lang="en">
<head>
<meta charset="utf-8">
<title>Kelvora Security – Make Security a Team Sport</title>
<link href="https://fonts.googleapis.com/css2?family=Fira+Sans:wght@600;700&family=Open+Sans:wght@400;600&display=swap" rel="stylesheet">
<style>
  :root{
    --orange:#ff5e1f;
    --purple:#3f2f94;
    --purple-deep:#2d2170;
    --charcoal:#3b3b3d;
    --charcoal-dark:#2a2a2c;
    --ink:#2b2b2b;
    --white:#ffffff;
    --page-bg:#f0f0f0;
  }
  *{margin:0;padding:0;box-sizing:border-box}
  html,body{width:1200px;height:1200px;overflow:hidden;background:var(--page-bg)}
  .canvas{position:relative;width:1200px;height:1200px}
  .flyer{
    position:absolute;left:155px;top:29px;width:741px;height:952px;
    transform:scale(1.2);transform-origin:0 0;overflow:hidden;
    background:var(--white);font-family:"Open Sans",sans-serif;
    box-shadow:0 4px 18px rgba(0,0,0,.18);
  }
  .backdrop{position:absolute;inset:0}
  .brand{position:absolute;left:30px;top:34px;display:flex;align-items:center;gap:12px}
  .brand-mark{width:38px;height:38px;background:var(--orange)}
  .brand-name{font-family:"Fira Sans",sans-serif;font-weight:700;font-size:30px;line-height:1;color:var(--ink);letter-spacing:1px}
  .art{position:absolute}
  .art-team{left:100px;top:140px;width:320px;height:325px;border-radius:40px;
    background:radial-gradient(circle at 55% 45%,#8b5cf6 0%,#4f46c8 45%,rgba(63,47,148,0) 75%)}
  .art-monitor{left:410px;top:76px;width:305px;height:245px;border-radius:6px;
    background:linear-gradient(180deg,#1b1b1d 0%,#555 72%,#d9d9d9 73%,#bdbdbd 100%)}
  .tagline{position:absolute;right:30px;top:392px;text-align:right;
    font-family:"Fira Sans",sans-serif;font-weight:700;font-size:44px;line-height:52px;color:var(--white)}
  .intro{position:absolute;left:28px;top:574px;width:297px;color:var(--white)}
  .intro .lead{font-size:16.5px;line-height:20px;text-align:justify;margin-bottom:18px}
  .intro p{font-size:12px;line-height:14px;text-align:justify;margin-bottom:20px}
  .about-tab{position:absolute;left:581px;top:560px;width:170px;height:40px;border-radius:20px 0 0 20px;
    background:var(--orange);color:var(--white);font-family:"Fira Sans",sans-serif;font-weight:700;
    font-size:21px;line-height:40px;padding-left:31px}
  .about{position:absolute;left:362px;top:620px;width:352px;color:var(--ink)}
  .about p{font-size:12px;line-height:14px;text-align:justify;margin-bottom:12px}
  .footer-label{position:absolute;left:28px;top:894px;display:flex;align-items:center;gap:6px;
    font-family:"Fira Sans",sans-serif;font-weight:700;font-size:21px;color:var(--ink);letter-spacing:.5px}
  .contact{position:absolute;left:380px;top:885px;color:var(--white);font-size:16px;line-height:21px}
  .contact li{list-style:none;display:flex;align-items:center;gap:8px}
  .social{position:absolute;left:652px;top:895px;display:flex;gap:6px}
  .social span{width:28px;height:28px;border-radius:50%;background:var(--white)}
</style>
</head>
<body>
<div class="canvas">
  <div class="flyer">
    <svg class="backdrop" viewBox="0 0 741 952" width="741" height="952">
      <defs>
        <linearGradient id="darkFill" x1="0" y1="0" x2="1" y2="1">
          <stop offset="0" stop-color="#4a4a4c"/><stop offset="1" stop-color="#2a2a2c"/>
        </linearGradient>
      </defs>
      <rect width="741" height="952" fill="url(#darkFill)"/>
      <!-- purple band -->
      <path d="M0 128 H330 C360 250 470 365 741 365 V490 C600 520 470 560 420 556 C250 545 90 420 0 350 Z" fill="var(--purple)"/>
      <!-- orange arc around monitor -->
      <path d="M330 120 C360 250 470 372 741 372" fill="none" stroke="var(--orange)" stroke-width="6"/>
      <!-- stripes under purple -->
      <path d="M0 350 C90 420 250 545 420 556 C470 560 600 520 741 490" fill="none" stroke="#4a4a4c" stroke-width="10"/>
      <path d="M0 366 C100 440 260 560 430 568 C500 568 620 540 741 505" fill="none" stroke="var(--orange)" stroke-width="5"/>
      <!-- top white header -->
      <path d="M0 0 H445 C410 90 310 128 200 132 L0 132 Z" fill="var(--white)"/>
      <path d="M445 0 C410 90 310 128 200 132" fill="none" stroke="var(--orange)" stroke-width="5"/>
      <!-- lower white area -->
      <path d="M741 510 C620 548 500 578 340 578 V952 H741 Z" fill="var(--white)"/>
      <path d="M0 835 H310 Q340 835 340 805 V578 H360 V952 H0 Z" fill="var(--white)"/>
      <!-- footer -->
      <rect x="0" y="932" width="741" height="20" fill="var(--orange)"/>
      <path d="M385 880 H741 V952 H360 V905 Q360 880 385 880 Z" fill="var(--orange)"/>
    </svg>

    <div class="brand"><span class="brand-mark"></span><span class="brand-name">KELVORA<br>SECURITY</span></div>

    <div class="art art-team" role="img" aria-label="Isometric illustration of a team working together around a large glowing padlock and screens"></div>
    <div class="art art-monitor" role="img" aria-label="Desktop monitor showing the Kelvora analytics dashboard with a line chart"></div>

    <h1 class="tagline">Make Security<br>a Team Sport</h1>

    <div class="intro">
      <p class="lead">KELVORA is a security data analytics platform, enabling security teams and business partners with timely, actionable alerts and intelligence.</p>
      <p>KELVORA moves as fast as you. With a variety of deployment models including on-premises, hybrid, or fully cloud-based, clients measure ROI in weeks, not months.</p>
      <p>KELVORA makes security a team sport. Leveraging advanced machine learning and workflow optimization, KELVORA ensures that the right information is making it to the right people every time.</p>
    </div>

    <div class="about-tab">About Us</div>
    <div class="about">
      <p>KELVORA security data analytics platform that will be featured in an upcoming security magazine. This is also going to be featured in an upcoming trade show.</p>
      <p>Kelvora Security produced the KELVORA platform to help companies unify their security environment and help them address Insider Threat, Fraud and Anomaly ID and resolution.</p>
      <p>KELVORA uses an an advanced ingestion engine, machine learning, and workflow automation to ensure the right people are getting the right info at the right time. We serve enterprise level customers, augmenting and enhancing, not replacing their existing security stack.</p>
      <p>KELVORA complements existing tools, including SIEM and UBA, to provide enhanced visibility into your organization's blind spots.</p>
    </div>

    <div class="footer-label">
      <svg width="16" height="16" viewBox="0 0 16 16"><circle cx="8" cy="8" r="8" fill="var(--orange)"/><path d="M5 4.5l1.5-.5 1 2-1 .8a5 5 0 002.7 2.7l.8-1 2 1-.5 1.5c-3.5 0-6.5-3-6.5-6.5z" fill="#fff"/></svg>
      IPSUM QUIA DOLOR
    </div>
    <ul class="contact">
      <li><svg width="13" height="13" viewBox="0 0 14 14"><circle cx="7" cy="7" r="7" fill="#fff"/><rect x="3.5" y="4.5" width="7" height="5" fill="none" stroke="var(--orange)" stroke-width="1.2"/><path d="M3.5 4.5 7 7.3l3.5-2.8" fill="none" stroke="var(--orange)" stroke-width="1.2"/></svg>ipsumquiadolorsitamet</li>
      <li><svg width="13" height="13" viewBox="0 0 14 14" fill="none" stroke="#fff" stroke-width="1.2"><circle cx="7" cy="7" r="6"/><ellipse cx="7" cy="7" rx="2.6" ry="6"/><path d="M1 7h12"/></svg>www.kelvorasecurity.net</li>
    </ul>
    <div class="social"><span></span><span></span></div>
  </div>
</div>
</body>
</html>
```